Ward Compass Business Card Design*

We need a business card design for our company Ward Compass. Our company is specialized in providing online consulting services regarding medical institutions, hospitals and doctors. We work with patients worldwide looking to choose between healthcare providers. We have a website you may use as a reference, where we list doctors and clinics worldwide. So we target Medical providers as well as patients worldwide.
Target Market(s)
Medical Providers and patients around the world
Industry/Entity Type
Medical
Contact Information for Business Card
Salwa Kettani
CEO
+90 612 348 2175
info@wardcompass.example
www.wardcompass.example
14 Annakhil 7 H.R.B. Rabat, Morocco
Requirements
Must have
- Company logo/name on one full side, personal info and smaller logo and company name on the other side.
Nice to have
- Smart and elegant design

```html
<!DOCTYPE html>
<html lang="en">
<head>
<meta charset="utf-8">
<title>Ward Compass – Business Card</title>
<link rel="stylesheet" href="https://fonts.googleapis.com/css2?family=Lato:wght@400;700&display=swap">
<style>
  :root {
    --backdrop: #2b2724;
    --card: #121212;
    --card-edge: #1c1c1c;
    --blue-deep: #2f6fbf;
    --blue-bright: #35a3e0;
    --text-light: #d9d9d9;
    --silver: #e6e6e6;
    --divider: #2a2a2a;
  }
  * { margin: 0; padding: 0; box-sizing: border-box; }
  html, body {
    width: 1200px; height: 844px; overflow: hidden;
    background: var(--backdrop);
    font-family: "Lato", Arial, sans-serif;
  }
  .sheet {
    width: 1200px; height: 844px;
    display: flex; align-items: center; justify-content: center; gap: 50px;
  }
  .card {
    width: 525px; height: 300px;
    background: var(--card);
    border: 1px solid var(--card-edge);
    position: relative;
    box-shadow: 0 10px 30px rgba(0,0,0,0.45);
  }

  /* Front: personal details */
  .card-front { display: flex; align-items: center; }
  .brand-block {
    width: 235px; height: 100%;
    display: flex; align-items: center; justify-content: center; gap: 12px;
  }
  .brand-dot {
    width: 22px; height: 22px; border-radius: 50%;
    background: var(--blue-bright);
  }
  .brand-name {
    color: var(--blue-bright);
    font-weight: 700; font-size: 21px; letter-spacing: 0.5px;
  }
  .divider {
    width: 1px; height: 150px; background: var(--divider);
  }
  .details { padding-left: 30px; }
  .person-name {
    color: var(--blue-bright); font-weight: 700;
    font-size: 19px; letter-spacing: 0.5px; text-transform: uppercase;
  }
  .person-role {
    color: var(--text-light); font-size: 13px; margin-top: 2px;
  }
  .contact-list { list-style: none; margin-top: 26px; }
  .contact-list li {
    display: flex; align-items: center; gap: 8px;
    color: var(--text-light); font-size: 14px; line-height: 20px;
  }
  .contact-list svg { width: 12px; height: 12px; fill: var(--blue-bright); flex: none; }

  /* Back: company name */
  .card-back { display: flex; align-items: center; justify-content: center; gap: 14px; }
  .back-dot {
    width: 34px; height: 34px; border-radius: 50%;
    background: var(--silver);
  }
  .back-name {
    color: var(--silver); font-weight: 400;
    font-size: 27px; letter-spacing: 2px; text-transform: uppercase;
  }
</style>
</head>
<body>
<main class="sheet">
  <section class="card card-front" aria-label="Card front">
    <div class="brand-block">
      <span class="brand-dot"></span>
      <span class="brand-name">Ward Compass</span>
    </div>
    <div class="divider"></div>
    <div class="details">
      <p class="person-name">Salwa Kettani</p>
      <p class="person-role">CEO</p>
      <ul class="contact-list">
        <li>
          <svg viewBox="0 0 24 24" aria-hidden="true"><path d="M6.6 10.8a15.1 15.1 0 0 0 6.6 6.6l2.2-2.2c.3-.3.7-.4 1-.2 1.1.4 2.3.6 3.6.6.6 0 1 .4 1 1V20c0 .6-.4 1-1 1A17 17 0 0 1 3 4c0-.6.4-1 1-1h3.5c.6 0 1 .4 1 1 0 1.3.2 2.5.6 3.6.1.3 0 .7-.2 1z"/></svg>
          +90 612 348 2175
        </li>
        <li>
          <svg viewBox="0 0 24 24" aria-hidden="true"><path d="M2 5h20v14H2z M4 7v.5l8 5 8-5V7l-8 5z" fill-rule="evenodd"/></svg>
          info@wardcompass.example
        </li>
        <li>
          <svg viewBox="0 0 24 24" aria-hidden="true"><circle cx="12" cy="12" r="10"/></svg>
          www.wardcompass.example
        </li>
      </ul>
    </div>
  </section>

  <section class="card card-back" aria-label="Card back">
    <span class="back-dot"></span>
    <span class="back-name">Ward Compass</span>
  </section>
</main>
</body>
</html>
```